New stationary design for online film company

We need some new stationary to fit with our new logo. The stationary should be professional, clean and simple.
We need designs for a full set of business stationary.
We need - letterhead, envelopes, invoices, proposals, coverslip/note and cover page

Industry/Entity Type

Business

```html
<!DOCTYPE html>
<html lang="en">
<head>
<meta charset="utf-8">
<title>brightreel — Stationery Set</title>
<link rel="stylesheet" href="https://fonts.googleapis.com/css2?family=Lato:wght@300;400;700&family=Dancing+Script:wght@500&display=swap">
<style>
  :root{
    --navy:#0b3d66;
    --navy-dark:#08304f;
    --sky:#5b97c9;
    --paper:#f7f7f8;
    --bg:#e9eaec;
    --ink:#4a5866;
    --faint-navy:rgba(255,255,255,.06);
    --faint-grey:rgba(11,61,102,.06);
  }
  *{box-sizing:border-box;margin:0;padding:0}
  html,body{width:1200px;height:795px;overflow:hidden}
  body{background:var(--bg);font-family:'Lato',sans-serif;color:var(--ink);position:relative}
  .piece{position:absolute;box-shadow:0 2px 6px rgba(0,0,0,.12)}
  .brand{display:flex;align-items:center;gap:6px;font-weight:700;color:var(--navy);letter-spacing:-.2px}
  .brand-dot{border-radius:50%;background:currentColor;flex:none}
  .brand.on-navy{color:#fff}
  .tagline{font-weight:300;text-transform:uppercase;letter-spacing:1.2px;color:var(--sky)}
  .faint-circle{position:absolute;border-radius:50%;border-style:solid}

  /* Letterhead */
  .letterhead{left:40px;top:40px;width:300px;height:424px;background:var(--paper);padding:30px 30px 20px;overflow:hidden}
  .letterhead .brand{font-size:17px}
  .letterhead .brand-dot{width:11px;height:11px}
  .letterhead .faint-circle{width:170px;height:170px;right:-40px;top:130px;border-width:26px;border-color:var(--faint-grey)}
  .letter-body{position:relative;margin-top:26px;font-size:6.6px;line-height:1.6}
  .letter-body p{margin-bottom:7px}
  .signature{font-family:'Dancing Script',cursive;font-size:17px;color:var(--navy);margin-top:6px}
  .signer-role{font-size:6.5px;font-weight:700;color:var(--navy)}
  .letter-footer{position:absolute;left:30px;right:30px;bottom:18px;display:flex;gap:16px;font-size:5.6px;line-height:1.5;border-top:1px solid #dde1e5;padding-top:7px}
  .letter-footer b{color:var(--navy)}

  /* Folder cover */
  .folder{left:370px;top:40px;width:300px;height:424px;background:var(--navy);overflow:hidden}
  .folder .faint-circle{width:240px;height:240px;left:-40px;top:60px;border-width:40px;border-color:var(--faint-navy)}
  .folder-brand{position:absolute;right:34px;bottom:120px;text-align:left}
  .folder-brand .brand{font-size:26px}
  .folder-brand .brand-dot{width:16px;height:16px}
  .folder-brand .tagline{font-size:7px;margin-top:5px;padding-left:22px}

  /* Envelope */
  .envelope{left:700px;top:40px;width:460px;height:200px;background:var(--paper);overflow:hidden}
  .envelope-band{height:58px;background:var(--navy);display:flex;align-items:center;padding-left:40px}
  .envelope-band .brand{font-size:22px}
  .envelope-band .brand-dot{width:14px;height:14px}

  /* Compliment slip */
  .slip{left:700px;top:264px;width:460px;height:200px;background:var(--paper);overflow:hidden;padding:26px 34px}
  .slip .faint-circle{width:150px;height:150px;right:-20px;top:-30px;border-width:24px;border-color:var(--faint-grey)}
  .slip-head{display:flex;align-items:flex-start;gap:22px}
  .slip .brand{font-size:20px}
  .slip .brand-dot{width:13px;height:13px}
  .contact{font-size:6.4px;line-height:1.55}
  .contact b{color:var(--navy)}
  .slip-note{position:absolute;left:34px;bottom:24px;font-size:15px;color:var(--navy)}

  /* Business cards */
  .card{width:240px;height:137px;top:520px}
  .card-front{left:40px;background:var(--navy);display:flex;flex-direction:column;justify-content:center;align-items:center}
  .card-front .brand{font-size:22px}
  .card-front .brand-dot{width:14px;height:14px}
  .card-front .tagline{font-size:6px;margin-top:5px}
  .card-back{left:300px;background:var(--paper);padding:18px 18px;border-left:5px solid var(--navy)}
  .card-back .brand{font-size:16px}
  .card-back .brand-dot{width:10px;height:10px}
  .card-person{margin-top:20px;font-size:8px;font-weight:700;color:var(--navy)}
  .card-role{font-size:6.5px;margin-bottom:10px}
  .card-back .contact{display:flex;gap:18px}

  /* Notebook */
  .notebook{left:580px;top:495px;width:210px;height:270px;background:var(--navy);overflow:hidden}
  .notebook-spiral{position:absolute;left:6px;top:8px;bottom:8px;width:8px;
    background:repeating-linear-gradient(to bottom,#6d7883 0 3px,transparent 3px 9px)}
  .notebook-brand{position:absolute;left:40px;top:100px}
  .notebook-brand .brand{font-size:22px}
  .notebook-brand .brand-dot{width:14px;height:14px}
  .notebook-brand .tagline{font-size:6px;margin-top:5px;padding-left:20px}

  /* Key tag, eraser, pencils */
  .keyring{position:absolute;left:830px;top:495px;width:34px;height:34px;border:3px solid #b9bec4;border-radius:50%}
  .keytag{left:815px;top:532px;width:66px;height:104px;background:var(--navy);border:4px solid #d7dadd;border-radius:6px;display:flex;align-items:center;justify-content:center}
  .keytag .brand-dot,.eraser .brand-dot{width:20px;height:20px;color:#fff;background:none;border:3px solid #fff}
  .eraser{left:910px;top:540px;width:62px;height:100px;background:var(--paper)}
  .eraser-sleeve{height:64px;background:var(--navy);display:flex;align-items:center;justify-content:center}
  .pencil{top:495px;width:11px;height:260px;background:linear-gradient(to right,var(--navy-dark),var(--navy));border-radius:2px}
  .pencil::before{content:"";position:absolute;top:-16px;left:0;border-left:5.5px solid transparent;border-right:5.5px solid transparent;border-bottom:16px solid #d9c6a4}
  .pencil-a{left:1010px}
  .pencil-b{left:1040px}
</style>
</head>
<body>

<section class="piece letterhead" aria-label="Letterhead">
  <div class="faint-circle"></div>
  <div class="brand"><span class="brand-dot"></span>brightreel</div>
  <div class="letter-body">
    <p><b>Dear Client,</b></p>
    <p>Thank you for considering our studio for your next online film project. We plan, shoot and edit short films that help brands tell clear stories to the audiences they care about most.</p>
    <p>Our team covers every stage, from early strategy and scripting to filming, motion graphics and final delivery across web and social channels.</p>
    <p>Please find our proposal enclosed. We would be glad to arrange a short call to discuss timings, budget and the next steps.</p>
    <p>Kind regards,</p>
    <div class="signature">Your Name</div>
    <div class="signer-role">Company Director</div>
  </div>
  <footer class="letter-footer">
    <div><b>t</b> 212 555 0148<br><b>m</b> 212 555 0173<br><b>e</b> hello@brightreel.tv</div>
    <div>18 Harbor Lane Suite 4<br>Portland ME 04101 USA<br><b>brightreel.tv</b></div>
  </footer>
</section>

<section class="piece folder" aria-label="Presentation folder cover">
  <div class="faint-circle"></div>
  <div class="folder-brand">
    <div class="brand on-navy"><span class="brand-dot"></span>brightreel</div>
    <div class="tagline">Online film production &amp; strategy</div>
  </div>
</section>

<section class="piece envelope" aria-label="DL envelope">
  <div class="envelope-band">
    <div class="brand on-navy"><span class="brand-dot"></span>brightreel</div>
  </div>
</section>

<section class="piece slip" aria-label="Compliment slip">
  <div class="faint-circle"></div>
  <div class="slip-head">
    <div class="brand"><span class="brand-dot"></span>brightreel</div>
    <div class="contact"><b>t</b> 212 555 0148<br><b>m</b> 212 555 0173<br><b>e</b> hello@brightreel.tv</div>
    <div class="contact">18 Harbor Lane Suite 4<br>Portland ME 04101 USA<br><b>brightreel.tv</b></div>
  </div>
  <div class="slip-note">With compliments</div>
</section>

<section class="piece card card-front" aria-label="Business card front">
  <div class="brand on-navy"><span class="brand-dot"></span>brightreel</div>
  <div class="tagline">Online film production &amp; strategy</div>
</section>

<section class="piece card card-back" aria-label="Business card back">
  <div class="brand"><span class="brand-dot"></span>brightreel</div>
  <div class="card-person">Mara Ellison</div>
  <div class="card-role">Producer</div>
  <div class="contact">
    <div><b>t</b> 212 555 0148<br><b>e</b> hello@brightreel.tv</div>
    <div>18 Harbor Lane Suite 4<br>Portland ME 04101</div>
  </div>
</section>

<section class="piece notebook" aria-label="Spiral notebook cover">
  <div class="notebook-spiral"></div>
  <div class="notebook-brand">
    <div class="brand on-navy"><span class="brand-dot"></span>brightreel</div>
    <div class="tagline">Online film production &amp; strategy</div>
  </div>
</section>

<div class="keyring" aria-hidden="true"></div>
<div class="piece keytag" aria-label="Key tag"><span class="brand-dot"></span></div>

<div class="piece eraser" aria-label="Branded eraser">
  <div class="eraser-sleeve"><span class="brand-dot"></span></div>
</div>

<div class="piece pencil pencil-a" aria-label="Branded pencil"></div>
<div class="piece pencil pencil-b" aria-label="Branded pencil"></div>

</body>
</html>
```